New Business Card Design Project

Need a design that will create an impact / strong impression towards our clients for our business. We are in the lighting business and we do lighting retrofits for large commercial to industrial clientele.

Target Market(s)

Lighting Industry

Industry/Entity Type

Business

Font styles to use
Other font styles liked:
• we would like to use the font on our logo, not sure what it is though..

Requirements
Must have
• Our logo.
Nice to have
• We are open to suggestions that have to do with lighting.

```html
<!DOCTYPE html>
<html lang="en">
<head>
<meta charset="utf-8">
<title>Brightway Retrofit Co. — Business Card</title>
<link rel="stylesheet" href="https://fonts.googleapis.com/css2?family=PT+Sans:wght@400;700&display=swap">
<style>
  :root {
    --stage: #3b3431;
    --card: #141414;
    --card-edge: #1c1c1c;
    --green: #2f9e44;
    --green-deep: #1f6e30;
    --silver: #9a9a9a;
    --white: #f2f2f2;
    --divider: #8a8a8a;
  }
  * { box-sizing: border-box; margin: 0; padding: 0; }
  html, body {
    width: 1200px; height: 864px; overflow: hidden;
    background: var(--stage);
    font-family: "PT Sans", "Helvetica Neue", Arial, sans-serif;
  }
  .stage {
    position: relative; width: 1200px; height: 864px;
    display: flex; align-items: center; justify-content: center; gap: 50px;
  }
  .card {
    position: relative; width: 540px; height: 309px; flex: none;
    background: var(--card);
    border: 1px solid var(--card-edge);
    box-shadow: 0 14px 30px rgba(0,0,0,.45);
    overflow: hidden;
  }
  /* Back side */
  .card-back { display: flex; flex-direction: column; align-items: center; justify-content: center; gap: 34px; }
  .back-brand {
    display: flex; align-items: center; gap: 12px; white-space: nowrap;
    color: var(--silver); font-size: 30px; font-weight: 700; letter-spacing: 1px;
  }
  .back-brand .mark-square { width: 18px; height: 18px; background: var(--silver); }
  .back-url { color: var(--silver); font-size: 14px; letter-spacing: 3px; }
  /* Front side */
  .card-front { display: flex; align-items: center; }
  .brand-block { flex: none; padding: 0 20px 0 30px; }
  .brand-name {
    display: flex; align-items: center; gap: 8px; white-space: nowrap;
    color: var(--green); font-size: 19px; font-weight: 700; line-height: 1.1;
  }
  .brand-name .mark-square { width: 14px; height: 14px; background: var(--green); flex: none; }
  .divider {
    flex: none; width: 1px; height: 190px;
    background: linear-gradient(to bottom, transparent, var(--divider), transparent);
  }
  .contact-block {
    flex: 1; min-width: 0; padding-left: 18px;
    color: var(--white); font-size: 14.5px; line-height: 1.3; white-space: nowrap;
  }
  .contact-name { color: var(--green); font-size: 16px; font-weight: 700; letter-spacing: .5px; }
  .contact-title { color: var(--green); font-size: 14.5px; margin-bottom: 4px; }
  .contact-line { display: flex; align-items: center; gap: 9px; }
  .contact-line svg { width: 11px; height: 11px; fill: var(--green-deep); flex: none; }
  .contact-line.plain { padding-left: 20px; }
</style>
</head>
<body>
<main class="stage">
  <section class="card card-back" aria-label="Card back">
    <div class="back-brand"><span class="mark-square"></span>Brightway Retrofit Co.</div>
    <p class="back-url">www.brightwayretrofit.com</p>
  </section>

  <section class="card card-front" aria-label="Card front">
    <div class="brand-block">
      <div class="brand-name"><span class="mark-square"></span>Brightway Retrofit Co.</div>
    </div>
    <div class="divider"></div>
    <div class="contact-block">
      <p class="contact-name">DANIEL REYES</p>
      <p class="contact-title">CEO/FOUNDER</p>
      <p class="contact-line">
        <svg viewBox="0 0 12 12"><path d="M6 0a4 4 0 0 0-4 4c0 3 4 8 4 8s4-5 4-8a4 4 0 0 0-4-4zm0 5.5A1.5 1.5 0 1 1 6 2.5a1.5 1.5 0 0 1 0 3z"/></svg>
        4120 Cedar Ridge Road
      </p>
      <p class="contact-line plain">Fairview, Oregon 97024</p>
      <p class="contact-line">
        <svg viewBox="0 0 12 12"><path d="M3 0h6a1 1 0 0 1 1 1v10a1 1 0 0 1-1 1H3a1 1 0 0 1-1-1V1a1 1 0 0 1 1-1zm0 2v7h6V2z"/></svg>
        555 214 7730
      </p>
      <p class="contact-line">
        <svg viewBox="0 0 12 12"><path d="M2.5 0 4.5 3 3.3 4.4a7 7 0 0 0 4.3 4.3L9 7.5l3 2-1 2C5 12 0 7 .5 1z"/></svg>
        555 380 1162
      </p>
      <p class="contact-line">
        <svg viewBox="0 0 12 12"><path d="M2 4h8v6H2zM3 0h6v3H3zm0 7h6v1H3z"/></svg>
        555 907 4418
      </p>
      <p class="contact-line">
        <svg viewBox="0 0 12 12"><path d="M0 2h12v8H0zm1 1 5 4 5-4z"/></svg>
        dan@brightwayretrofit.com
      </p>
      <p class="contact-line">
        <svg viewBox="0 0 12 12"><circle cx="6" cy="6" r="6"/></svg>
        www.brightwayretrofit.com
      </p>
    </div>
  </section>
</main>
</body>
</html>
```